Rebrand stationary with recently completed logo design

Need new business cards, thank you cards, letterhead, envelopes and presentation folders. The designs will be sent to a separate production firm so I need the files to be print ready.

My contact info
Reko Haliburn

Office 604-318-5047
Fax 604-371-8054

Email reko@glazemark.ca
website www.glazemark.ca

315-14720 62nd Avenue,
Langley, BC, V2K 3R8

Target Market(s)

Homeowners, businesses and contractors

Industry/Entity Type

Business

Font styles to use
Sans Serif

Colors
34a7d7

Requirements
Must have
• Like to have one side of the business card a solid color with the logo in all white. The side with all the text to be a white background
• I find the current blue on the front of the card with the white logo too dark.
Should not have
• Gradient colors

```html
<!DOCTYPE html>
<html lang="en">
<head>
<meta charset="utf-8">
<title>Glazemark business card</title>
<link rel="stylesheet" href="https://fonts.googleapis.com/css2?family=Open+Sans:wght@400;600;700&display=swap">
<style>
  :root {
    --backdrop: #7a5238;
    --paper: #f3f3f3;
    --slate: #3d4b55;
    --brand-blue: #1996d4;
    --ink: #555b60;
    --white: #ffffff;
  }
  * { margin: 0; padding: 0; box-sizing: border-box; }
  html, body {
    width: 1200px; height: 960px; overflow: hidden;
    background: var(--backdrop);
    font-family: "Open Sans", Arial, sans-serif;
  }
  .canvas { position: relative; width: 1200px; height: 960px; }
  .card {
    position: absolute; width: 600px; height: 343px;
    box-shadow: 0 3px 8px rgba(0,0,0,.35);
  }
  .card--front { left: 302px; top: 129px; background: var(--paper); }
  .card--back { left: 299px; top: 488px; background: var(--slate); }

  .wordmark {
    position: absolute; font-weight: 400; letter-spacing: 0.5px;
    text-transform: uppercase; line-height: 1;
  }
  .card--front .wordmark { left: 45px; top: 56px; font-size: 40px; color: var(--brand-blue); }

  .name-band {
    position: absolute; left: 0; top: 187px; width: 235px; height: 54px;
    background: var(--brand-blue);
  }
  .name-band__text {
    position: absolute; left: 45px; top: 0; line-height: 54px;
    color: var(--white); font-weight: 600; font-size: 19px; text-transform: uppercase;
  }
  .name-band__block {
    position: absolute; left: 238px; top: 187px; width: 28px; height: 54px;
    background: var(--slate);
  }

  .contact { position: absolute; left: 397px; top: 183px; color: var(--ink); font-size: 13px; }
  .contact__address { line-height: 18px; margin-bottom: 10px; }
  .contact__line { display: flex; align-items: center; height: 19px; }
  .contact__icon { width: 15px; height: 13px; margin-right: 7px; fill: var(--brand-blue); }
  .contact__web { margin-top: 5px; color: var(--brand-blue); font-weight: 600; }

  .back-mark {
    position: absolute; left: 0; right: 0; top: 0; bottom: 0;
    display: flex; align-items: center; justify-content: center; gap: 18px;
  }
  .back-mark__square { width: 44px; height: 44px; background: var(--white); }
  .back-mark .wordmark { position: static; font-size: 46px; color: var(--white); }
</style>
</head>
<body>
<main class="canvas">
  <section class="card card--front" aria-label="Business card front">
    <div class="wordmark">Glazemark</div>

    <div class="name-band"><span class="name-band__text">Reko Haliburn</span></div>
    <div class="name-band__block"></div>

    <div class="contact">
      <p class="contact__address">315-14720 62nd Avenue<br>Langley, BC, V2K 3R8</p>
      <p class="contact__line">
        <svg class="contact__icon" viewBox="0 0 16 16" aria-hidden="true"><path d="M3.5 1l2.5 3-1.5 1.8c.9 2 2.4 3.5 4.4 4.4L10.7 9l3.3 2.4-1.2 2.8C7 14 2 9 1.8 3.2z"/></svg>
        604-318-5047
      </p>
      <p class="contact__line">
        <svg class="contact__icon" viewBox="0 0 16 14" aria-hidden="true"><rect x="4" y="0" width="8" height="4"/><rect x="0" y="5" width="16" height="6" rx="1"/><rect x="4" y="9" width="8" height="5"/></svg>
        604-371-8054
      </p>
      <p class="contact__line">
        <svg class="contact__icon" viewBox="0 0 16 12" aria-hidden="true"><path d="M0 1h16v10H0z M1 2l7 5 7-5" stroke="#f3f3f3" stroke-width="1"/></svg>
        reko@glazemark.ca
      </p>
      <p class="contact__web">www.glazemark.ca</p>
    </div>
  </section>

  <section class="card card--back" aria-label="Business card back">
    <div class="back-mark">
      <span class="back-mark__square"></span>
      <span class="wordmark">Glazemark</span>
    </div>
  </section>
</main>
</body>
</html>
```